Flyer for the Radiant Harvest Worship Day

I am looking to create a flyer for a one day prayer retreat our church is organizing.
This flyer will be posted on social media, websites and will also be printed so it can be mailed to people.
I am looking for something professional, with good use of our logo and band colors (logo colors).
I am counting on the designer's skill, creativity, art and knowledge of media communication to produce a flyer that will effectively and quickly convey the message we are trying to spread.
CONTENT OF THE FLYER:
Event title: Radiant Harvest Worship Day
Date: Tuesday July 2nd, 2019
Time: 11:00AM - 7:00PM
Belmora Hotel, 4875 Wexley Avenue, Portland, Maine 04102 (Room: Juniper)
Event Key words to highlight what the event is about: Prayer, Sharing the Word, Panel discussion, prophecy, Impartation.
Key phrases:
A one day prayer retreat.
Jesus Chris is Lord
Contact info:
www.tolvex.org
Phone: 207 555 3184
Email: contact@brookhavenfold.org

```html
<!DOCTYPE html>
<html lang="en">
<head>
<meta charset="utf-8">
<title>Radiant Harvest Worship Day</title>
<link rel="stylesheet" href="https://fonts.googleapis.com/css2?family=Cinzel:wght@400;600;700&display=swap">
<style>
:root{
  --navy:#17375a;
  --orange:#f39a2b;
  --ink:#2a2a2a;
  --page:#ffffff;
  --stage:#e9e9e9;
}
*{margin:0;padding:0;box-sizing:border-box}
html,body{width:1200px;height:1200px;overflow:hidden;background:var(--stage)}
body{font-family:'Cinzel',serif;position:relative}
.flyer{
  position:absolute;left:190px;top:20px;width:916px;height:1296px;
  transform:scale(0.895);transform-origin:0 0;
  background:var(--page);overflow:hidden;color:var(--navy);
}
.photo{
  position:absolute;left:0;top:0;width:100%;height:100%;
  background:
    linear-gradient(180deg,#fff 0%,rgba(255,255,255,.95) 18%,rgba(255,255,255,0) 30%,rgba(255,255,255,0) 62%,rgba(255,255,255,.85) 82%,#fff 100%),
    radial-gradient(ellipse 60% 38% at 55% 48%,#e3b8a3 0%,#dcae98 35%,#c9a79c 60%,#b9c3d3 85%,#cfd8e4 100%);
}
.abs{position:absolute}
.pre-title{top:68px;width:100%;text-align:center;font-size:40px;font-weight:400;letter-spacing:1px}
.retreat{top:122px;width:100%;text-align:center;font-size:53px;font-weight:700}
.motto{top:170px;width:100%;text-align:center;font-size:72px;font-weight:600;color:var(--orange)}
.info{
  left:112px;top:742px;width:692px;height:128px;
  background:rgba(255,255,255,.72);
}
.info .date{left:20px;top:28px;font-size:25px;font-weight:600}
.info .time{left:18px;top:62px;font-size:36px;font-weight:400}
.info .rule{left:331px;top:26px;width:2px;height:84px;background:var(--navy);opacity:.6}
.info .venue{left:350px;top:30px;font-size:15px;line-height:19px;font-weight:600}
.features{
  left:118px;top:896px;width:682px;height:160px;
  border:2px solid var(--navy);border-radius:10px;
}
.features ul{position:absolute;list-style:none;top:20px}
.features li{font-size:24px;height:38px;display:flex;align-items:center;gap:12px;color:#2a3550}
.features li svg{width:26px;height:22px;flex:none}
.features .col-a{left:34px}
.features .col-b{left:420px;top:18px}
.features .rule{position:absolute;left:364px;top:30px;width:2px;height:96px;background:var(--orange)}
.brand{left:68px;top:1140px;display:flex;align-items:center;gap:8px}
.brand .dot{width:20px;height:20px;border-radius:50%;background:var(--orange)}
.brand .name{font-size:42px;font-weight:600;color:var(--navy)}
.cta{left:255px;top:1126px;height:44px;padding:0 14px;background:var(--navy);color:#fff;border-radius:10px;font-size:33px;font-weight:600;line-height:44px}
.phone{left:560px;top:1120px;font-size:42px;color:var(--ink)}
.contacts{left:258px;top:1198px;display:flex;gap:24px;font-size:18px;color:#333;align-items:center}
.contacts span{display:flex;align-items:center;gap:10px}
.contacts svg{width:16px;height:16px}
</style>
</head>
<body>
<main class="flyer">
  <div class="photo" role="img" aria-label="Soft photo of hands folded in prayer over an open book"></div>

  <p class="abs pre-title">Radiant Harvest Worship Day</p>
  <h1 class="abs retreat">A one day prayer retreat</h1>
  <h2 class="abs motto">Jesus Chris is Lord</h2>

  <section class="abs info">
    <p class="abs date">Tuesday July 2nd, 2019</p>
    <p class="abs time">11:00AM - 7:00PM</p>
    <div class="abs rule"></div>
    <p class="abs venue">Belmora Hotel, 4875 Wexley Avenue,<br>Portland, Maine 04102<br>(Room: Juniper)</p>
  </section>

  <section class="abs features">
    <ul class="col-a">
      <li><svg viewBox="0 0 26 22"><path d="M2 12l7 7L24 3" fill="none" stroke="#f39a2b" stroke-width="4" stroke-linecap="round"/></svg>Prayer</li>
      <li><svg viewBox="0 0 26 22"><path d="M2 12l7 7L24 3" fill="none" stroke="#f39a2b" stroke-width="4" stroke-linecap="round"/></svg>Sharing the Word</li>
      <li><svg viewBox="0 0 26 22"><path d="M2 12l7 7L24 3" fill="none" stroke="#f39a2b" stroke-width="4" stroke-linecap="round"/></svg>Panel discussion</li>
    </ul>
    <div class="rule"></div>
    <ul class="col-b">
      <li><svg viewBox="0 0 26 22"><path d="M2 12l7 7L24 3" fill="none" stroke="#f39a2b" stroke-width="4" stroke-linecap="round"/></svg>Prophecy</li>
      <li><svg viewBox="0 0 26 22"><path d="M2 12l7 7L24 3" fill="none" stroke="#f39a2b" stroke-width="4" stroke-linecap="round"/></svg>Impartation</li>
    </ul>
  </section>

  <div class="abs brand"><span class="dot"></span><span class="name">Tolvex</span></div>
  <p class="abs cta">Call us now</p>
  <p class="abs phone">207 555 3184</p>
  <div class="abs contacts">
    <span><svg viewBox="0 0 16 16"><rect x="1" y="3" width="14" height="10" fill="#17375a"/><path d="M1 3l7 6 7-6" fill="none" stroke="#fff" stroke-width="1.5"/></svg>contact@brookhavenfold.org</span>
    <span><svg viewBox="0 0 16 16"><circle cx="8" cy="8" r="7" fill="none" stroke="#17375a" stroke-width="2"/><path d="M1 8h14M8 1c-3 4-3 10 0 14M8 1c3 4 3 10 0 14" fill="none" stroke="#17375a" stroke-width="1.2"/></svg>www.tolvex.org</span>
  </div>
</main>
</body>
</html>
```